Brintel Works - Fast, Efficient and Gas Mainteance for Domestic, Commercial and Industrial clients

We are in the process of purchasing a new business and would like to get a new logo and business card.
Business is a gas maintenance business that also does new gas installations.
Has been established since 1988.
Services include:
Install all types of gas appliances & equipment inc. hot water units
Maintain / repair / replace all types of gas appliances & equipment

Target Market(s)

Domestic, Commercial and Industrial clients

Industry/Entity Type

Business

Contact Information for Business Card

admin@brintelworks.com.au
07 3918 4726
Brintel Works PTY LTD

Logo Text

Gas Fitting & Plumbing Maintenance Specialists

Font styles to use
Sans Serif

Requirements
Must have
• Logo
• Business name, contact number, email address, web address
• Domestic | Commercial | Industrial Est Since 1988
Nice to have
• Possibly a black card with a flame logo to one side
Should not have
• Spelling errors

```html
<!DOCTYPE html>
<html lang="en">
<head>
<meta charset="utf-8">
<title>Brintel Works – Business Card</title>
<link href="https://fonts.googleapis.com/css2?family=Open+Sans:wght@400;700&family=Tinos&family=Great+Vibes&display=swap" rel="stylesheet">
<style>
  :root {
    --page: #e8e8e6;
    --card: #f4f4f4;
    --slate: #4a5261;
    --red: #e8452c;
    --ink: #4a5261;
    --muted: #8a8f98;
    --white: #ffffff;
  }
  html, body {
    margin: 0;
    width: 1200px;
    height: 902px;
    overflow: hidden;
    background: var(--page);
  }
  .card {
    position: absolute;
    left: 100px;
    top: 165px;
    width: 1000px;
    height: 572px;
    background: var(--card);
    box-shadow: 0 10px 30px rgba(0,0,0,0.18);
    overflow: hidden;
  }
  .card-bands {
    position: absolute;
    inset: 0;
  }
  .brand {
    position: absolute;
    left: 120px;
    top: 70px;
    font-family: "Open Sans", sans-serif;
  }
  .brand-name {
    font-weight: 700;
    font-size: 54px;
    color: var(--red);
    letter-spacing: 0.5px;
    line-height: 1;
  }
  .brand-suffix {
    position: absolute;
    left: 448px;
    top: 0;
    font-size: 11px;
    font-weight: 700;
    color: var(--ink);
  }
  .tagline {
    margin-top: 10px;
    font-weight: 700;
    font-size: 31px;
    color: var(--ink);
    line-height: 1.1;
  }
  .sectors {
    margin-top: 12px;
    font-size: 16px;
    color: var(--muted);
    display: flex;
    align-items: baseline;
    gap: 22px;
  }
  .established {
    font-family: "Great Vibes", cursive;
    font-size: 30px;
    color: var(--muted);
  }
  .contact {
    position: absolute;
    right: 45px;
    top: 210px;
    list-style: none;
    margin: 0;
    padding: 0;
    font-family: "Tinos", serif;
    color: var(--white);
    text-align: right;
  }
  .contact li {
    display: flex;
    justify-content: flex-end;
    align-items: center;
    gap: 22px;
    font-size: 27px;
    height: 52px;
  }
  .contact li.address {
    font-size: 30px;
    margin-top: 12px;
  }
  .contact .icon {
    width: 26px;
    height: 26px;
    background: var(--white);
    border-radius: 3px;
    display: flex;
    align-items: center;
    justify-content: center;
    flex: none;
  }
</style>
</head>
<body>
  <div class="card">
    <svg class="card-bands" width="1000" height="572" viewBox="0 0 1000 572">
      <polygon points="0,410 1000,90 1000,110 0,430" fill="var(--red)"/>
      <polygon points="0,430 1000,110 1000,572 0,572" fill="var(--slate)"/>
    </svg>

    <div class="brand">
      <div class="brand-name">Brintel Works</div>
      <div class="brand-suffix">PTY LTD</div>
      <div class="tagline">Gas fitting &amp; Plumbing Specialists</div>
      <div class="sectors">
        <span>Domestic | Commercial | Industrial</span>
        <span class="established">Est Since 1988</span>
      </div>
    </div>

    <ul class="contact">
      <li>07 3918 4726
        <span class="icon"><svg width="16" height="16" viewBox="0 0 16 16"><path d="M3 2h3l1 3-2 1c1 2 2 3 4 4l1-2 3 1v3c0 1-1 2-2 2C6 14 2 10 2 4c0-1 .5-2 1-2z" fill="var(--slate)"/></svg></span>
      </li>
      <li>admin@brintelworks.com.au
        <span class="icon"><svg width="16" height="16" viewBox="0 0 16 16"><rect x="2" y="4" width="12" height="8" fill="var(--slate)"/><path d="M2 4l6 5 6-5" stroke="var(--white)" stroke-width="1.2" fill="none"/></svg></span>
      </li>
      <li>www.brintelworks.com.au
        <span class="icon"><svg width="16" height="16" viewBox="0 0 16 16"><circle cx="8" cy="8" r="6" fill="none" stroke="var(--slate)" stroke-width="1.6"/><ellipse cx="8" cy="8" rx="2.5" ry="6" fill="none" stroke="var(--slate)" stroke-width="1.2"/><line x1="2" y1="8" x2="14" y2="8" stroke="var(--slate)" stroke-width="1.2"/></svg></span>
      </li>
      <li class="address">PO Box 2864, Marlow Heads, QLD 4221
        <span class="icon"><svg width="16" height="16" viewBox="0 0 16 16"><path d="M8 15s-5-5.5-5-9a5 5 0 0 1 10 0c0 3.5-5 9-5 9z" fill="var(--slate)"/><circle cx="8" cy="6" r="1.8" fill="var(--white)"/></svg></span>
      </li>
    </ul>
  </div>
</body>
</html>
```